Agriculture farming Hemp and CBD

The logo is in works with your company now, should be ready in a few days. We have our Domain (kestrelbrookhollow.com) We would like to see incorporated seed to growth, but not necessary. we would like to nature colors and some black and green. we have our farm and will be growing and selling HEMP and CBD we are based in the state of Virginia. Would like to incorporate the words pause, play, rewind if possible but not necessary.

Target Market(s)

20 years old to elderly

Coding

Coded - Design and coding required

Number of Pages Required

3 page

Font styles to use
Serif

Requirements
Must have
• I'm not sure on the must haves, we are open to any ideas, we would definitely like to see Hemp and CBD included, may the life cycle of seed to plant. We must have a pop up asking if you are 20 years old before they can enter our site and to view or purchase our product. I want the design to be totally different than what i uploaded.
Nice to have
• Would like to see natural colors as well as black and green
Should not have
• I want

```html
<!DOCTYPE html>
<html lang="en">
<head>
<meta charset="utf-8">
<title>Kestrel Brook Hollow – Home</title>
<link href="https://fonts.googleapis.com/css2?family=Poppins:wght@500;600&family=Roboto:wght@400;500;700&family=Lora:wght@400&display=swap" rel="stylesheet">
<style>
:root{
  --green:#179a24;
  --green-bright:#1fbf1f;
  --black:#0a0a0a;
  --dark:#17171a;
  --darker:#121214;
  --text:#ffffff;
  --stage:#e3e3e3;
}
*{box-sizing:border-box;margin:0;padding:0}
html,body{width:746px;height:1200px;overflow:hidden;background:var(--stage)}
body{font-family:Roboto,Arial,sans-serif;color:var(--text)}
.stage{position:absolute;left:0;top:0;width:1512px;height:2432px;transform:scale(.4934);transform-origin:0 0;background:var(--stage)}
.page{position:absolute;top:104px;width:599px;height:2211px;background:var(--dark);overflow:hidden}
.page--main{left:107px}
.page--gate{left:806px}
.abs{position:absolute}
.hl{color:var(--green-bright)}
.h-sec{font-family:Poppins,sans-serif;font-weight:600;font-size:20px;color:#fff}
.body-s{font-size:6.5px;line-height:11.5px;color:#e6e6e6}
.btn{position:absolute;display:flex;align-items:center;justify-content:center;gap:4px;background:var(--green-bright);color:#fff;font-weight:700;font-size:7px;border-radius:12px;text-transform:uppercase}
.btn::after{content:"";width:6px;height:6px;border-radius:50%;border:1.5px solid #fff}
.photo{position:absolute}

.topbar{left:0;top:0;width:599px;height:19px;background:var(--green);display:flex;justify-content:flex-end;align-items:center;gap:12px;padding-right:55px;font-size:6.5px}
.topbar .dots{display:flex;gap:4px}
.topbar .dots i{width:5px;height:5px;border-radius:50%;background:#fff;display:block}
.header{left:0;top:19px;width:599px;height:43px;background:var(--black)}
.brand{font-family:Roboto,sans-serif;font-weight:700;font-size:11px;color:#fff;display:flex;align-items:center;gap:4px}
.brand b{width:6px;height:6px;background:var(--green-bright);border-radius:50%;display:block}
.nav{left:215px;top:16px;display:flex;gap:13px;font-size:7px;font-weight:500}
.nav .active{color:var(--green-bright);border-bottom:1.5px solid var(--green-bright);padding-bottom:4px}
.cart{left:472px;top:12px;display:flex;gap:6px;font-size:6px;align-items:center}
.cart-ico{width:17px;height:17px;border-radius:50%;background:var(--green-bright)}

.hero{left:0;top:62px;width:599px;height:290px;background:linear-gradient(180deg,#7d858a 0%,#9aa2a3 18%,#3f5a2a 30%,#5c7b34 55%,#8a5a3a 100%)}
.hero-box{left:148px;top:144px;width:303px;height:122px;background:rgba(0,0,0,.25)}
.hero-title{left:0;top:152px;width:599px;text-align:center;font-family:Poppins,sans-serif;font-weight:500;font-size:18px;word-spacing:14px}
.hero-text{left:150px;top:189px;width:300px;text-align:center;font-size:7.5px;line-height:14px}
.arrow{position:absolute;top:196px;width:20px;height:20px;border:1px solid #fff;border-radius:50%}

.cap{position:absolute;font-size:7px;text-align:center;width:156px;font-weight:700}
.cap span{color:var(--green-bright);font-weight:400}
.variety{left:0;top:882px;width:599px;height:283px;background:#1d1f1e}
.vcard{position:absolute;width:232px;height:72px;background:rgba(15,15,17,.8);border-radius:36px}
.vcard .disc{position:absolute;left:4px;top:4px;width:64px;height:64px;border-radius:50%;background:radial-gradient(circle,#6d9442,#22361a)}
.vcard h4{position:absolute;left:78px;top:11px;font-size:8px}
.vcard p{position:absolute;left:78px;top:24px;width:140px;font-size:6.5px;line-height:11.5px;color:#ddd}
.vcard .more{position:absolute;left:78px;top:55px;font-size:6.5px;font-weight:700;color:var(--green-bright)}
.tile{position:absolute;width:109px;height:112px;background:#fff}
.tile .img{height:90px}
.tile span{display:block;text-align:center;font-size:8px;font-weight:700;color:var(--green);margin-top:4px}
.faq-q{position:absolute;left:299px;width:245px;height:23px;border-radius:12px;background:#222226;font-size:7.5px;display:flex;align-items:center;justify-content:space-between;padding:0 14px}
.faq-q.open{background:var(--green-bright)}
.footer h5{position:absolute;font-size:7.5px;font-weight:700}
.footer .list{position:absolute;font-size:6px;line-height:12.5px;color:#ddd}

.dim{left:0;top:0;width:599px;height:2211px;background:rgba(0,0,0,.78)}
.modal{left:192px;top:136px;width:215px;height:138px;background:#fff;color:#222}
.modal .brand{color:#111;justify-content:center}
.modal h3{font-family:Lora,serif;font-weight:400;font-size:11px;color:#666;text-align:center}
</style>
</head>
<body>
<div class="stage">

<main class="page page--main">
  <div class="abs topbar"><span>(555) 010-2040</span><span>sales@kestrelbrookhollow.com</span><span class="dots"><i></i><i></i><i></i><i></i></span></div>
  <header class="abs header">
    <div class="abs brand" style="left:56px;top:14px">kestrelbrookhollow<b></b></div>
    <nav class="abs nav"><span class="active">Home</span><span>Products</span><span>About</span><span>Blog</span><span>Wholesale</span><span>Contact</span></nav>
    <div class="abs cart"><span class="cart-ico"></span><span>My Cart<br>0 Item | <span class="hl">$0.00</span></span></div>
  </header>

  <section class="abs hero" role="img" aria-label="Rows of hemp plants growing in a farm field under a cloudy sky"></section>
  <div class="abs hero-box"></div>
  <h1 class="abs hero-title">Pause Play Rewind</h1>
  <p class="abs hero-text">Lorem ipsum dolor sit amet, consectetur adipiscing elit, sed do eiusmod tempor incididunt ut labore et dolore magna aliqua.</p>
  <div class="btn" style="left:250px;top:232px;width:100px;height:24px">Get Started</div>
  <span class="arrow" style="left:16px"></span><span class="arrow" style="left:563px"></span>

  <h2 class="abs h-sec" style="left:0;width:599px;text-align:center;top:403px">Who <span class="hl">We Are</span></h2>
  <p class="abs body-s" style="left:80px;width:440px;top:438px;text-align:center">Lorem ipsum dolor sit amet, consectetur adipiscing elit, sed do eiusmod tempor incididunt ut labore et dolore magna aliqua. Ut enim ad minim veniam, quis nostrud exercitation ullamco laboris nisi ut aliquip ex ea commodo consequat. Duis aute irure dolor in reprehenderit in voluptate velit esse cillum dolore eu fugiat nulla pariatur.</p>
  <div class="photo" style="left:55px;top:488px;width:156px;height:100px;background:linear-gradient(160deg,#d8c07a,#4e6d28 50%,#24381a)" role="img" aria-label="Hemp plants in warm sunlight"></div>
  <div class="photo" style="left:221px;top:488px;width:156px;height:100px;background:linear-gradient(180deg,#c9d4cf,#3f8b34 45%,#1f4b1a)" role="img" aria-label="Young hemp plants in a greenhouse"></div>
  <div class="photo" style="left:387px;top:488px;width:156px;height:100px;background:linear-gradient(180deg,#e8e8e8,#3d7a2e 45%,#203a18)" role="img" aria-label="Indoor grow room with rows of hemp"></div>
  <div class="cap" style="left:55px;top:598px"><span>All Year</span> Premier Strains</div>
  <div class="cap" style="left:221px;top:598px"><span>You Choose From A</span> Large Selection</div>
  <div class="cap" style="left:387px;top:598px"><span>Well</span> Rooted</div>

  <div class="abs" style="left:355px;top:667px;width:244px;height:215px;background:var(--green)"></div>
  <div class="abs" style="left:55px;top:675px;font-size:8px;color:#ccc">ABOUT US</div>
  <h2 class="abs" style="left:55px;top:690px;font-family:Poppins,sans-serif;font-weight:600;font-size:16px">100% Organic <span class="hl">Hemp CBD</span></h2>
  <div class="abs" style="left:55px;top:715px;font-size:7px;color:var(--green-bright)">Get Healthy and Stay Healthy</div>
  <p class="abs body-s" style="left:55px;top:737px;width:225px">Lorem ipsum dolor sit amet, consectetur adipiscing elit, sed do eiusmod tempor incididunt ut labore et dolore magna aliqua. Ut enim ad minim veniam, quis nostrud exercitation ullamco laboris nisi ut aliquip ex ea commodo consequat. Duis aute irure dolor in reprehenderit in voluptate velit esse laborum.</p>
  <div class="btn" style="left:55px;top:810px;width:84px;height:23px">Read More</div>
  <div class="photo" style="left:304px;top:698px;width:257px;height:155px;background:linear-gradient(180deg,#8b8a6e,#5a6b34 40%,#3b4a22)" role="img" aria-label="Large indoor hemp grow facility"></div>

  <section class="abs variety" role="img" aria-label="Dark misty hemp field backdrop"></section>
  <h2 class="abs h-sec" style="left:0;width:599px;text-align:center;top:912px">Variety <span class="hl">types</span></h2>
  <div class="vcard" style="left:56px;top:956px"><span class="disc" role="img" aria-label="CBD oil bottles"></span><h4>High CBD</h4><p>Lorem ipsum dolor sit amet, consectetur adipiscing elit, sed do eiusmod aliqua.</p><span class="more">READ MORE</span></div>
  <div class="vcard" style="left:310px;top:956px"><span class="disc" role="img" aria-label="Sativa bud"></span><h4>Sativa</h4><p>Lorem ipsum dolor sit amet, consectetur adipiscing elit, sed do eiusmod aliqua.</p><span class="more">READ MORE</span></div>
  <div class="vcard" style="left:56px;top:1052px"><span class="disc" role="img" aria-label="Hybrid bud"></span><h4>Hybrid</h4><p>Lorem ipsum dolor sit amet, consectetur adipiscing elit, sed do eiusmod aliqua.</p><span class="more">READ MORE</span></div>
  <div class="vcard" style="left:310px;top:1052px"><span class="disc" role="img" aria-label="Indica bud"></span><h4>Indica</h4><p>Lorem ipsum dolor sit amet, consectetur adipiscing elit, sed do eiusmod aliqua.</p><span class="more">READ MORE</span></div>

  <div class="photo" style="left:50px;top:1230px;width:235px;height:135px;background:#3a3a3e;border-radius:10px" role="img" aria-label="Map of the United States with Virginia highlighted in green"></div>
  <h2 class="abs h-sec" style="left:308px;top:1228px;font-size:16px;line-height:22px">The Best Hemp <span class="hl">Grown In<br>Virginia</span></h2>
  <p class="abs body-s" style="left:308px;top:1280px;width:236px">Sed ut perspiciatis unde omnis iste natus sit voluptatem accusantium doloremque laudantium, totam rem aperiam, eaque ipsa quae ab illo inventore veritatis et quasi architecto beatae vitae dicta sunt explicabo. Nemo enim ipsam voluptatem quia voluptas sit aspernatur aut odit aut</p>
  <div class="btn" style="left:308px;top:1344px;width:92px;height:23px">Contact Us</div>

  <div class="abs" style="left:0;top:1423px;width:599px;height:150px;background:linear-gradient(180deg,#2a2624,#1b1b1d)"></div>
  <h2 class="abs h-sec" style="left:0;width:599px;text-align:center;top:1446px;font-size:16px">Premium Organically <span class="hl">Grown Hemp</span></h2>
  <p class="abs body-s" style="left:85px;width:430px;top:1477px;text-align:center">Sed ut perspiciatis unde omnis iste natus error sit voluptatem accusantium doloremque laudantium, totam rem aperiam, eaque ipsa quae ab illo inventore veritatis et quasi architecto beatae vitae dicta sunt explicabo.</p>
  <div class="tile" style="left:117px;top:1516px"><div class="img" style="background:linear-gradient(160deg,#3a4a30,#6d5a4a)" role="img" aria-label="Frozen hemp flower close-up"></div><span>Fresh Frozen</span></div>
  <div class="tile" style="left:245px;top:1516px"><div class="img" style="background:linear-gradient(180deg,#d4dcd6,#3f8a30 40%,#24501c)" role="img" aria-label="Hemp biomass plants"></div><span>Biomass</span></div>
  <div class="tile" style="left:373px;top:1516px"><div class="img" style="background:linear-gradient(160deg,#8a9a4a,#4c5e2a)" role="img" aria-label="Dried premium hemp flower"></div><span>Premium Flower</span></div>

  <div class="photo" style="left:55px;top:1684px;width:215px;height:200px;background:linear-gradient(150deg,#6f9a3a,#3f6a24 55%,#b47c74)" role="img" aria-label="Woman inspecting a hemp plant"></div>
  <h2 class="abs h-sec" style="left:299px;top:1688px;font-size:18px">Hemp and <span class="hl">CBD FAQ</span></h2>
  <div class="faq-q open" style="top:1734px"><span>Proprietary Risk Databases. 11 ecosystems.</span><span>–</span></div>
  <p class="abs" style="left:326px;top:1766px;width:205px;font-size:6px;line-height:11.5px;color:#ddd">Beyond the core search, our team cross-references user-entered names with its proprietary, dynamic risk databases. It executes more than 1 million queries across</p>
  <div class="faq-q" style="top:1816px"><span>Proprietary Risk Databases. 11 ecosystems.</span><span>+</span></div>
  <div class="faq-q" style="top:1850px"><span>Proprietary Risk Databases. 11 ecosystems.</span><span>+</span></div>

  <section class="abs" style="left:0;top:1941px;width:599px;height:74px;background:var(--green)">
    <h2 class="abs" style="left:69px;top:16px;font-family:Poppins,sans-serif;font-weight:600;font-size:17px;line-height:20px">Sign Up For The<br><span style="font-size:12px">kestrel brook hollow</span></h2>
    <div class="abs" style="left:284px;top:14px;font-size:6.5px;font-weight:500">GET EXCLUSIVE, NEW PRODUCT RELEASES, AND CONTESTS!</div>
    <div class="abs" style="left:284px;top:32px;width:245px;height:26px;border-radius:13px;background:#fff;overflow:hidden">
      <span class="abs" style="left:11px;top:9px;font-size:5.5px;color:#666">Email Address</span>
      <span class="abs" style="left:168px;top:0;width:77px;height:26px;background:var(--black);font-size:7px;font-weight:700;display:flex;align-items:center;justify-content:center">SUBSCRIBE</span>
    </div>
  </section>

  <footer class="abs footer" style="left:0;top:2015px;width:599px;height:196px;background:var(--darker)">
    <div class="abs brand" style="left:55px;top:58px;font-size:10px">kestrelbrookhollow<b></b></div>
    <p class="abs" style="left:55px;top:84px;width:110px;font-size:6px;line-height:11.5px;color:#ddd">Sed ut perspiciatis unde omnis iste natus sit voluptatem accusantium doloremque laudantium,</p>
    <h5 style="left:204px;top:48px">Quick Links</h5>
    <div class="list" style="left:204px;top:66px">Home<br>About<br>Products<br>Recipe<br>Blogs &amp; News</div>
    <h5 style="left:306px;top:48px">Social Media</h5>
    <div class="abs" style="left:306px;top:69px;display:flex;gap:5px"><i style="width:5px;height:5px;border-radius:50%;background:#bbb;display:block"></i><i style="width:5px;height:5px;border-radius:50%;background:#bbb;display:block"></i><i style="width:5px;height:5px;border-radius:50%;background:#bbb;display:block"></i></div>
    <h5 style="left:306px;top:92px">Opening Hours</h5>
    <div class="list" style="left:309px;top:108px">Monday - Sunday<br>10:00 am - 8:00 pm</div>
    <h5 style="left:422px;top:48px">Contact Details</h5>
    <div class="list" style="left:434px;top:64px;line-height:9.5px"><b>Phone</b><br>+555 010 2040<br><br><b>Email</b><br>info@kestrelbrookhollow.com<br><br><b>Location</b><br>P.O.Box 218<br>Lorem ipsum dolor sit amet</div>
    <div class="abs" style="left:55px;top:158px;width:489px;height:1px;background:#444"></div>
    <div class="abs" style="left:0;width:599px;top:170px;text-align:center;font-size:6.5px">2020 Copyright - kestrelbrookhollow | All Rights Reserved</div>
  </footer>
</main>

<div class="page page--gate" aria-hidden="true">
  <div class="abs topbar"><span>(555) 010-2040</span><span>sales@kestrelbrookhollow.com</span></div>
  <div class="abs header"><div class="abs brand" style="left:56px;top:14px">kestrelbrookhollow<b></b></div><nav class="abs nav"><span class="active">Home</span><span>Products</span><span>About</span><span>Blog</span><span>Wholesale</span><span>Contact</span></nav></div>
  <div class="abs hero"></div>
  <h2 class="abs h-sec" style="left:0;width:599px;text-align:center;top:403px">Who <span class="hl">We Are</span></h2>
  <div class="photo" style="left:55px;top:488px;width:156px;height:100px;background:#4e6d28"></div>
  <div class="photo" style="left:221px;top:488px;width:156px;height:100px;background:#3f8b34"></div>
  <div class="photo" style="left:387px;top:488px;width:156px;height:100px;background:#3d7a2e"></div>
  <div class="abs" style="left:355px;top:667px;width:244px;height:215px;background:var(--green)"></div>
  <h2 class="abs" style="left:55px;top:690px;font-family:Poppins,sans-serif;font-weight:600;font-size:16px">100% Organic <span class="hl">Hemp CBD</span></h2>
  <div class="photo" style="left:304px;top:698px;width:257px;height:155px;background:#5a6b34"></div>
  <div class="abs variety"></div>
  <h2 class="abs h-sec" style="left:0;width:599px;text-align:center;top:912px">Variety <span class="hl">types</span></h2>
  <div class="vcard" style="left:56px;top:956px"><span class="disc"></span></div>
  <div class="vcard" style="left:310px;top:956px"><span class="disc"></span></div>
  <div class="vcard" style="left:56px;top:1052px"><span class="disc"></span></div>
  <div class="vcard" style="left:310px;top:1052px"><span class="disc"></span></div>
  <div class="photo" style="left:50px;top:1230px;width:235px;height:135px;background:#3a3a3e;border-radius:10px"></div>
  <h2 class="abs h-sec" style="left:308px;top:1228px;font-size:16px;line-height:22px">The Best Hemp <span class="hl">Grown In<br>Virginia</span></h2>
  <h2 class="abs h-sec" style="left:0;width:599px;text-align:center;top:1446px;font-size:16px">Premium Organically <span class="hl">Grown Hemp</span></h2>
  <div class="tile" style="left:117px;top:1516px"><div class="img" style="background:#4a4a38"></div><span>Fresh Frozen</span></div>
  <div class="tile" style="left:245px;top:1516px"><div class="img" style="background:#3f8a30"></div><span>Biomass</span></div>
  <div class="tile" style="left:373px;top:1516px"><div class="img" style="background:#6a7a3a"></div><span>Premium Flower</span></div>
  <div class="photo" style="left:55px;top:1684px;width:215px;height:200px;background:#4f7a2c"></div>
  <h2 class="abs h-sec" style="left:299px;top:1688px;font-size:18px">Hemp and <span class="hl">CBD FAQ</span></h2>
  <div class="faq-q open" style="top:1734px"></div><div class="faq-q" style="top:1816px"></div><div class="faq-q" style="top:1850px"></div>
  <div class="abs" style="left:0;top:1941px;width:599px;height:74px;background:var(--green)"></div>
  <div class="abs" style="left:0;top:2015px;width:599px;height:196px;background:var(--darker)"></div>
  <div class="abs dim"></div>

  <div class="abs modal" role="dialog" aria-label="Age verification">
    <span class="abs" style="right:6px;top:3px;font-size:8px;color:#333">×</span>
    <div class="abs" style="left:31px;top:12px;width:152px;height:33px;border:1px solid #e4e4e4;display:flex;align-items:center;justify-content:center"><div class="brand" style="font-size:10.5px">kestrelbrookhollow<b></b></div></div>
    <h3 class="abs" style="left:0;width:215px;top:51px">Age Verification</h3>
    <div class="abs" style="left:90px;top:70px;width:35px;height:1.5px;background:#bbb"></div>
    <p class="abs" style="left:0;width:215px;top:79px;text-align:center;font-size:7px">You Must be <b style="color:#c00">20</b> Years old to enter.</p>
    <div class="abs" style="left:33px;top:98px;width:67px;height:19px;border-radius:10px;background:#ccc;color:#fff;font-size:7px;display:flex;align-items:center;justify-content:center">NO</div>
    <div class="abs" style="left:115px;top:98px;width:67px;height:19px;border-radius:10px;background:var(--green-bright);color:#fff;font-size:7px;font-weight:700;display:flex;align-items:center;justify-content:center">YES</div>
  </div>
</div>

</div>
</body>
</html>
```